Harborlane Products Flyer

Harborlane Lending Group, Inc.
Licensed Mortgage Company
Serving the DMV since 1997
"You open the Harborlane, we'll carry the load"
We specialize in...
FHA Loans
* Credit Scores as low as 500
* 203K Renovation Loans
Conventional Loans
* As little as 1% Down
* Bank Statement for Self-Employed
Investor Loans
* DSCR, & Fix & Flip
* Commercial & New Construction
Other Programs
* HELOCS & Reverse Mortgages
Call today for a free consultation
(800) 914-6027
www.harborlanehomeloans.com
NMLS #731860

```html
<!DOCTYPE html>
<html lang="en">
<head>
<meta charset="utf-8">
<title>Harborlane Products Flyer</title>
<link rel="stylesheet" href="https://fonts.googleapis.com/css2?family=Montserrat:wght@700;800&family=Nunito:wght@300;400;700;800&display=swap">
<style>
  :root {
    --navy: #02141d;
    --navy-soft: #0a1e2a;
    --gold: #d7a84f;
    --gold-light: #f3dfae;
    --gold-deep: #b9822c;
    --blue: #2d63d6;
    --blue-dark: #1a45b5;
    --cream: #f4ece1;
    --white: #ffffff;
    --gold-gradient: linear-gradient(100deg, #e7bf6a 0%, #f6e6bf 35%, #d39b44 65%, #f2d9a0 100%);
  }
  * { box-sizing: border-box; margin: 0; padding: 0; }
  html, body { width: 930px; height: 1200px; overflow: hidden; background: var(--navy); }
  .flyer {
    position: relative;
    width: 930px;
    height: 1200px;
    background: var(--navy);
    overflow: hidden;
    font-family: "Nunito", sans-serif;
  }

  /* Hero photo */
  .hero-photo {
    position: absolute;
    left: 400px; top: 45px;
    width: 530px; height: 430px;
    background:
      linear-gradient(90deg, var(--navy) 0%, rgba(2,20,29,0.55) 25%, rgba(2,20,29,0) 50%),
      linear-gradient(0deg, var(--navy) 0%, rgba(2,20,29,0) 30%),
      linear-gradient(180deg, #4b5a57 0%, #8a8e83 35%, #5c7443 70%, #3d5a2c 100%);
  }

  /* Brand */
  .brand {
    position: absolute;
    left: 70px; top: 58px;
    width: 280px;
    text-align: center;
  }
  .brand-name {
    font-family: "Montserrat", sans-serif;
    font-weight: 800;
    font-size: 32px;
    letter-spacing: 1px;
    color: var(--gold);
    line-height: 1.1;
  }
  .brand-sub {
    font-family: "Montserrat", sans-serif;
    font-weight: 800;
    font-size: 17px;
    letter-spacing: 2px;
    color: var(--gold);
    margin-top: 4px;
  }
  .brand-tagline {
    font-size: 10px;
    color: var(--blue);
    margin-top: 10px;
    text-transform: uppercase;
    letter-spacing: 0.2px;
  }
  .brand-est {
    font-size: 9px;
    font-weight: 700;
    letter-spacing: 3px;
    color: var(--gold-light);
    margin-top: 6px;
  }

  /* Headline */
  .headline {
    position: absolute;
    left: 68px; top: 214px;
    font-family: "Montserrat", sans-serif;
    font-weight: 800;
    font-size: 54px;
    line-height: 61px;
    text-transform: uppercase;
    background: var(--gold-gradient);
    -webkit-background-clip: text;
    background-clip: text;
    color: transparent;
  }

  /* Specialties area */
  .arc {
    position: absolute;
    left: 0; top: 0;
    width: 930px; height: 1200px;
  }
  .specialize-pill {
    position: absolute;
    left: 290px; top: 578px;
    width: 351px; height: 44px;
    border-radius: 22px;
    background: linear-gradient(90deg, var(--blue-dark), var(--blue));
    color: var(--white);
    font-family: "Montserrat", sans-serif;
    font-weight: 800;
    font-size: 22px;
    line-height: 44px;
    text-align: center;
    letter-spacing: 0.5px;
  }
  .loan-card {
    position: absolute;
    width: 369px; height: 163px;
    background: var(--navy);
    border: 3px solid var(--gold);
    border-radius: 10px;
    padding: 18px 16px 0 14px;
  }
  .loan-card--fha { left: 77px; top: 661px; }
  .loan-card--conventional { left: 483px; top: 661px; }
  .loan-card--investor { left: 77px; top: 861px; }
  .loan-card--other { left: 483px; top: 861px; }
  .loan-title {
    font-weight: 800;
    font-size: 23px;
    line-height: 1.1;
    background: var(--gold-gradient);
    -webkit-background-clip: text;
    background-clip: text;
    color: transparent;
    margin-bottom: 8px;
  }
  .loan-list { list-style: none; }
  .loan-list li {
    position: relative;
    padding-left: 28px;
    font-weight: 400;
    font-size: 17px;
    line-height: 19px;
    color: var(--white);
    margin-bottom: 9px;
  }
  .loan-list li strong { font-weight: 800; }
  .loan-list li svg {
    position: absolute;
    left: 0; top: 1px;
    width: 19px; height: 19px;
  }

  /* Footer */
  .footer-rule {
    position: absolute;
    left: 0; top: 1062px;
    width: 930px; height: 6px;
    background: linear-gradient(90deg, #c99443, #f3dfae 45%, #c08434);
  }
  .phone-icon {
    position: absolute;
    left: 79px; top: 1112px;
    width: 50px; height: 50px;
  }
  .cta-line {
    position: absolute;
    left: 144px; top: 1110px;
    font-weight: 800;
    font-size: 19px;
    color: var(--gold);
  }
  .cta-phone {
    position: absolute;
    left: 142px; top: 1132px;
    font-weight: 800;
    font-size: 32px;
    line-height: 1.1;
    background: var(--gold-gradient);
    -webkit-background-clip: text;
    background-clip: text;
    color: transparent;
  }
  .contact {
    position: absolute;
    left: 593px; top: 1114px;
    color: var(--white);
  }
  .contact-web { font-weight: 800; font-size: 18px; }
  .contact-nmls { font-weight: 400; font-size: 17px; margin-top: 10px; }
</style>
</head>
<body>
<main class="flyer">

  <div class="hero-photo" role="img" aria-label="Photo of a happy family celebrating in front of a house with a for-sale sign"></div>

  <div class="brand">
    <div class="brand-name">HARBORLANE</div>
    <div class="brand-sub">LENDING GROUP</div>
    <div class="brand-tagline">You open the Harborlane, we'll carry the load</div>
    <div class="brand-est">EST. 1997</div>
  </div>

  <h1 class="headline">You open<br>the Harborlane<br>we'll carry<br>the load</h1>

  <svg class="arc" viewBox="0 0 930 1200" aria-hidden="true">
    <defs>
      <linearGradient id="arcGold" x1="0" y1="0" x2="1" y2="0">
        <stop offset="0" stop-color="#e2b866"/>
        <stop offset="0.45" stop-color="#f6e6c4"/>
        <stop offset="0.8" stop-color="#c8862f"/>
        <stop offset="1" stop-color="#e0a955"/>
      </linearGradient>
      <radialGradient id="creamFill" cx="0.5" cy="0.45" r="0.7">
        <stop offset="0" stop-color="#f7efe5"/>
        <stop offset="0.6" stop-color="#efe3d4"/>
        <stop offset="1" stop-color="#e6d3bf"/>
      </radialGradient>
    </defs>
    <path d="M0,671 Q465,250 930,671" fill="none" stroke="var(--blue)" stroke-width="2"/>
    <path d="M0,700 Q465,262 930,700 L930,1062 L0,1062 Z" fill="url(#creamFill)" role="img" aria-label="Soft faded photo of a smiling family"/>
    <path d="M0,700 Q465,262 930,700" fill="none" stroke="url(#arcGold)" stroke-width="14"/>
  </svg>

  <div class="specialize-pill">WE SPECIALIZE IN...</div>

  <section class="loan-card loan-card--fha">
    <h2 class="loan-title">FHA Loans</h2>
    <ul class="loan-list">
      <li><svg viewBox="0 0 20 20"><circle cx="9" cy="11" r="7.5" fill="none" stroke="#2d63d6" stroke-width="2"/><path d="M5.5 10.5l3 3L18 3" fill="none" stroke="#2d63d6" stroke-width="2.2" stroke-linecap="round"/></svg>Credit Scores as low as <strong>500</strong></li>
      <li><svg viewBox="0 0 20 20"><circle cx="9" cy="11" r="7.5" fill="none" stroke="#2d63d6" stroke-width="2"/><path d="M5.5 10.5l3 3L18 3" fill="none" stroke="#2d63d6" stroke-width="2.2" stroke-linecap="round"/></svg>203K Renovation Loans</li>
    </ul>
  </section>

  <section class="loan-card loan-card--conventional">
    <h2 class="loan-title">Conventional Loans</h2>
    <ul class="loan-list">
      <li><svg viewBox="0 0 20 20"><circle cx="9" cy="11" r="7.5" fill="none" stroke="#2d63d6" stroke-width="2"/><path d="M5.5 10.5l3 3L18 3" fill="none" stroke="#2d63d6" stroke-width="2.2" stroke-linecap="round"/></svg>As little as <strong>1% Down</strong></li>
      <li><svg viewBox="0 0 20 20"><circle cx="9" cy="11" r="7.5" fill="none" stroke="#2d63d6" stroke-width="2"/><path d="M5.5 10.5l3 3L18 3" fill="none" stroke="#2d63d6" stroke-width="2.2" stroke-linecap="round"/></svg>Bank Statement for<br>Self-Employed</li>
    </ul>
  </section>

  <section class="loan-card loan-card--investor">
    <h2 class="loan-title">Investor Loans</h2>
    <ul class="loan-list">
      <li><svg viewBox="0 0 20 20"><circle cx="9" cy="11" r="7.5" fill="none" stroke="#2d63d6" stroke-width="2"/><path d="M5.5 10.5l3 3L18 3" fill="none" stroke="#2d63d6" stroke-width="2.2" stroke-linecap="round"/></svg>DSCR, &amp; Fix &amp; Flip</li>
      <li><svg viewBox="0 0 20 20"><circle cx="9" cy="11" r="7.5" fill="none" stroke="#2d63d6" stroke-width="2"/><path d="M5.5 10.5l3 3L18 3" fill="none" stroke="#2d63d6" stroke-width="2.2" stroke-linecap="round"/></svg>Commercial &amp;<br>New Construction</li>
    </ul>
  </section>

  <section class="loan-card loan-card--other">
    <h2 class="loan-title">Other Programs</h2>
    <ul class="loan-list">
      <li><svg viewBox="0 0 20 20"><circle cx="9" cy="11" r="7.5" fill="none" stroke="#2d63d6" stroke-width="2"/><path d="M5.5 10.5l3 3L18 3" fill="none" stroke="#2d63d6" stroke-width="2.2" stroke-linecap="round"/></svg>HELOCS &amp; Reverse<br>Mortgages</li>
    </ul>
  </section>

  <div class="footer-rule"></div>

  <svg class="phone-icon" viewBox="0 0 50 50" aria-hidden="true">
    <path d="M10 8c-4 3-5 8-2 14 5 10 12 17 21 21 5 2 9 1 12-2l-6-7c-1-1-3-1-4 0l-3 2c-5-2-10-7-12-12l2-3c1-1 1-3 0-4l-6-9z" fill="none" stroke="#d7a84f" stroke-width="2.5" stroke-linejoin="round"/>
    <path d="M28 9a13 13 0 0 1 13 13M28 3a19 19 0 0 1 19 19" fill="none" stroke="#d7a84f" stroke-width="2.5" stroke-linecap="round"/>
  </svg>
  <div class="cta-line">Call today for a free consultation</div>
  <div class="cta-phone">(800) 914-6027</div>

  <div class="contact">
    <div class="contact-web">www.harborlanehomeloans.com</div>
    <div class="contact-nmls">NMLS #731860</div>
  </div>

</main>
</body>
</html>
```